business card - Helicopter Flight Services, Flight School, etc.

We need a business card design for a new helicopter service.

We offer Helicopter Flight Services, Aerial Filming & Photography, Flight School, and Helicopter Tours. In that order.

Summit BladeAir, Inc.
Dennis Tollerby
SummitBladeair@Kestmail.com
626-418-7352

Based at the Brenwick Airport in Van Nuys, CA. The final design should communicate integrity and safety. Pictures or logos at your discretion.

Card back side - surprise me.

```html
<!DOCTYPE html>
<html lang="en">
<head>
<meta charset="utf-8">
<title>Summit BladeAir, Inc. – Business Card</title>
<link rel="stylesheet" href="https://fonts.googleapis.com/css2?family=Arimo:ital,wght@0,400;1,400;1,700&family=Open+Sans:wght@400&display=swap">
<style>
  :root {
    --page-bg: #8e8e8e;
    --card-light: #f6f6f6;
    --card-edge: #c9c9c9;
    --ink: #111111;
    --ink-soft: #474747;
    --band-purple: #6a70b6;
    --band-black: #1a1a1a;
    --white: #ffffff;
    --divider: #8a8a8a;
    --photo-dark: #1e2330;
    --photo-mid: #3f4a63;
  }
  * { margin: 0; padding: 0; box-sizing: border-box; }
  html, body {
    width: 1189px; height: 1200px; overflow: hidden;
    background: var(--page-bg);
  }
  .card {
    position: absolute;
    left: 136px;
    width: 917px; height: 523px;
    background: radial-gradient(ellipse at 50% 30%, var(--card-light) 0%, #e2e2e2 55%, var(--card-edge) 100%);
    overflow: hidden;
  }
  .card--front { top: 46px; }
  .card--back { top: 623px; }

  .wave { position: absolute; inset: 0; width: 917px; height: 523px; }

  .company-name {
    position: absolute;
    font-family: "Arimo", Arial, sans-serif;
    font-style: italic; font-weight: 400;
    color: var(--ink);
    white-space: nowrap;
    line-height: 1;
  }
  .card--front .company-name { left: 74px; top: 142px; font-size: 41px; }

  .aircraft-photo {
    position: absolute;
    left: 560px; top: 22px;
    width: 300px; height: 300px;
    border-radius: 46% 46% 30% 30%;
    background: radial-gradient(ellipse at 45% 60%, var(--photo-mid) 0%, var(--photo-dark) 70%, rgba(30,35,48,0) 100%);
  }

  .holder-name {
    position: absolute;
    left: 125px; top: 414px;
    font-family: "Arimo", Arial, sans-serif;
    font-style: italic; font-weight: 700;
    font-size: 27px; line-height: 1;
    color: var(--white);
    white-space: nowrap;
  }
  .divider {
    position: absolute;
    left: 436px; top: 362px;
    width: 1px; height: 123px;
    background: var(--divider);
  }
  .contact-list { position: absolute; left: 474px; top: 0; list-style: none; }
  .contact-item {
    position: absolute;
    left: 0;
    font-family: "Open Sans", Arial, sans-serif;
    font-size: 21px; line-height: 1;
    color: var(--white);
    white-space: nowrap;
    padding-left: 33px;
  }
  .contact-item svg {
    position: absolute; left: 0; top: 2px;
    width: 18px; height: 18px;
  }
  .contact-phone { top: 369px; letter-spacing: 1px; }
  .contact-email { top: 403px; }
  .contact-address { top: 436px; letter-spacing: 0.6px; }
  .contact-city { top: 468px; letter-spacing: 0.6px; }

  .card--back .company-name {
    left: 0; right: 0; top: 220px;
    text-align: center;
    font-size: 58px;
    letter-spacing: 0.5px;
  }
  .services {
    position: absolute;
    left: 0; right: 0; top: 287px;
    text-align: center;
    font-family: "Open Sans", Arial, sans-serif;
    font-size: 36px; line-height: 1;
    color: var(--ink-soft);
  }
</style>
</head>
<body>

<section class="card card--front">
  <div class="aircraft-photo" role="img" aria-label="Photo of a dark blue two-seat helicopter, seen from the front quarter"></div>
  <svg class="wave" viewBox="0 0 917 523" aria-hidden="true">
    <path fill="var(--band-purple)" d="M0,290 C140,320 250,345 390,320 S620,255 730,252 S870,280 917,322 L917,523 L0,523 Z"/>
    <path fill="var(--band-black)" d="M0,344 C120,368 250,385 400,356 S640,280 760,282 S880,308 917,336 L917,523 L0,523 Z"/>
  </svg>
  <h1 class="company-name">Summit BladeAir, Inc.</h1>
  <p class="holder-name">Dennis Tollerby</p>
  <div class="divider"></div>
  <ul class="contact-list">
    <li class="contact-item contact-phone">
      <svg viewBox="0 0 18 18" aria-hidden="true"><rect width="18" height="18" fill="var(--band-purple)"/><path fill="var(--band-black)" d="M5 3.5h2.2l1 3-1.4 1.1c.7 1.4 1.7 2.4 3 3l1.1-1.4 3 1v2.3c0 .8-.6 1.2-1.3 1.2C7.8 13.5 4 9.5 3.8 4.8 3.8 4 4.3 3.5 5 3.5z"/></svg>
      626-418-7352
    </li>
    <li class="contact-item contact-email">
      <svg viewBox="0 0 18 18" aria-hidden="true"><rect width="18" height="18" fill="var(--band-purple)"/><rect x="3.5" y="5" width="11" height="8" fill="var(--band-black)"/><path d="M3.8 5.3 9 9.5l5.2-4.2" fill="none" stroke="var(--band-purple)" stroke-width="1.2"/></svg>
      SummitBladeair@Kestmail.com
    </li>
    <li class="contact-item contact-address">
      <svg viewBox="0 0 18 18" aria-hidden="true"><rect width="18" height="18" fill="var(--band-purple)"/><path fill="var(--band-black)" d="M9 3.5c2.2 0 3.8 1.6 3.8 3.7 0 2.6-3.8 7.3-3.8 7.3S5.2 9.8 5.2 7.2C5.2 5.1 6.8 3.5 9 3.5z"/><circle cx="9" cy="7.2" r="1.4" fill="var(--band-purple)"/></svg>
      2840 W. Halvern Ave. Ste.B
    </li>
    <li class="contact-item contact-city">Brenwick, CA 91406</li>
  </ul>
</section>

<section class="card card--back">
  <h2 class="company-name">Summit BladeAir, Inc.</h2>
  <p class="services">Airport · Tour guide · Heliport</p>
</section>

</body>
</html>
```